Irrigation Business needs their business cards modernised and revamped

I would like to keep my current logo, colours and revamp the format of the card.

I would like the card to be clean yet important.

Im not sure if you include texture but i would like the named logo to be indented into the card etc.

show me something alive and free something thats clinical to the point yet has a feel of achievement. i would like people to go nice card.

Target Market(s)

high end clients, corporate, sports field manger, the guys that make the decisions

Industry/Entity Type

Business

Contact Information for Business Card

nformation to be included

Dean Harlow (Director)
0487305526
dean@kolvat.biz
www.kestonfieldworks.com

instagram logo
google logo
facebook logo

Colors

Designer to choose colors to be used in the design.

Requirements
Nice to have
• indentations a really nice feel to the card good texture

```html
<!DOCTYPE html>
<html lang="en">
<head>
<meta charset="utf-8">
<title>Keston Fieldworks – Business Card</title>
<link rel="stylesheet" href="https://fonts.googleapis.com/css2?family=Roboto:wght@700&family=Open+Sans:wght@400;600&display=swap">
<style>
  :root {
    --backdrop: #4a4a4a;
    --brand-blue: #2f69ae;
    --brand-blue-light: #3a9fd6;
    --brand-blue-deep: #2a5fa8;
    --paper: #ffffff;
    --ink: #4a4a4a;
    --name-dark: #2b5ea8;
    --name-light: #2d9ad6;
  }
  * { margin: 0; padding: 0; box-sizing: border-box; }
  html, body { width: 1200px; height: 900px; overflow: hidden; }
  body {
    background: radial-gradient(ellipse at center, #525252 0%, var(--backdrop) 70%, #444 100%);
    position: relative;
    font-family: "Open Sans", Arial, sans-serif;
  }
  .card {
    position: absolute;
    top: 306px;
    width: 440px;
    height: 271px;
    border-radius: 10px;
    overflow: hidden;
  }
  .card--front { left: 149px; background: var(--paper); }
  .card--back {
    left: 608px;
    background: linear-gradient(135deg, var(--brand-blue-deep) 0%, #3289cf 50%, var(--brand-blue-deep) 100%);
  }
  .front-band {
    position: absolute; left: 0; top: 0; width: 100%; height: 94px;
    background: var(--brand-blue);
  }
  .wordmark {
    position: absolute;
    font-family: "Roboto", Arial, sans-serif;
    font-weight: 700;
    color: var(--paper);
    text-align: center;
    line-height: 1;
  }
  .wordmark__main { display: block; font-size: 27px; letter-spacing: -0.5px; }
  .wordmark__sub { display: block; font-size: 27px; margin-top: 4px; letter-spacing: -0.5px; }
  .card--front .wordmark { left: 25px; top: 30px; width: 246px; }
  .card--back .wordmark { left: 0; top: 160px; width: 100%; }
  .brand-disc {
    position: absolute;
    border-radius: 50%;
  }
  .card--front .brand-disc {
    left: 314px; top: 16px; width: 100px; height: 100px;
    background: var(--paper);
  }
  .card--front .brand-disc::after {
    content: ""; position: absolute; inset: 11px; border-radius: 50%;
    background: var(--brand-blue-light);
  }
  .card--back .brand-disc {
    left: 177px; top: 67px; width: 86px; height: 86px;
    border: 3px solid var(--paper);
  }
  .card-pattern {
    position: absolute; inset: 0;
    background: linear-gradient(180deg, rgba(255,255,255,0.06), rgba(255,255,255,0));
  }
  .holder { position: absolute; left: 25px; top: 150px; }
  .holder__name { font-weight: 600; font-size: 16px; color: var(--name-dark); letter-spacing: 0.2px; }
  .holder__name span { color: var(--name-light); }
  .holder__role { font-size: 12px; color: var(--ink); margin-top: 0; }
  .contacts { position: absolute; left: 24px; top: 196px; list-style: none; }
  .contacts li {
    display: flex; align-items: center; gap: 3px;
    font-size: 12.5px; color: var(--ink); height: 16px;
  }
  .contacts svg { width: 12px; height: 12px; flex: none; }
  .social { position: absolute; left: 341px; top: 220px; display: flex; gap: 5px; }
  .social__dot { width: 22px; height: 22px; border-radius: 50%; background: var(--brand-blue); }
</style>
</head>
<body>
  <section class="card card--front" aria-label="Business card front">
    <div class="front-band"></div>
    <div class="wordmark"><span class="wordmark__main">KESTON</span><span class="wordmark__sub">FIELDWORKS</span></div>
    <div class="brand-disc" aria-hidden="true"></div>

    <div class="holder">
      <p class="holder__name">DEAN <span>HARLOW</span></p>
      <p class="holder__role">Director</p>
    </div>

    <ul class="contacts">
      <li>
        <svg viewBox="0 0 12 12" aria-hidden="true"><circle cx="6" cy="6" r="6" fill="#2f69ae"/><path d="M3.5 4.5h5v3h-5z" fill="#fff"/></svg>
        0487305526
      </li>
      <li>
        <svg viewBox="0 0 12 12" aria-hidden="true"><circle cx="6" cy="6" r="6" fill="#2f69ae"/><rect x="3" y="4" width="6" height="4" fill="#fff"/><path d="M3 4l3 2.2L9 4" stroke="#2f69ae" stroke-width="0.8" fill="none"/></svg>
        dean@kolvat.biz
      </li>
      <li>
        <svg viewBox="0 0 12 12" aria-hidden="true"><circle cx="6" cy="6" r="6" fill="#2f69ae"/><circle cx="6" cy="6" r="3" fill="none" stroke="#fff" stroke-width="1"/><path d="M3 6h6M6 3v6" stroke="#fff" stroke-width="0.8"/></svg>
        www.kestonfieldworks.com
      </li>
    </ul>

    <div class="social" aria-label="Social profiles">
      <span class="social__dot"></span>
      <span class="social__dot"></span>
      <span class="social__dot"></span>
    </div>
  </section>

  <section class="card card--back" aria-label="Business card back">
    <div class="card-pattern" role="img" aria-label="Repeating water droplet pattern in light blue"></div>
    <div class="brand-disc" aria-hidden="true"></div>
    <div class="wordmark"><span class="wordmark__main">KESTON</span><span class="wordmark__sub">FIELDWORKS</span></div>
  </section>
</body>
</html>
```